Manufacturers Catalog Cover Page

We are looking to have a cover to our catalog page designed. I currently have begun work for the remained of the catalog in InDesign and want the cover created in InDesign. I will provide photos.

Looking to beable to add the cover to our existing attached catalog.

Gathering more feedback

Industry/Entity Type

Manufacturing

Requirements
Must have
• Colors match what we are currently using. The Dark grey and gold
Nice to have
• modern, clean

```html
<!DOCTYPE html>
<html lang="en">
<head>
<meta charset="utf-8">
<title>Paragon Polymers – Catalog Cover</title>
<link href="https://fonts.googleapis.com/css2?family=Bebas+Neue&display=swap" rel="stylesheet">
<style>
  :root{
    --backdrop:#b4b4b4;
    --charcoal:#333334;
    --gold:#c9b08a;
    --gold-deep:#b89c72;
    --white:#f4f4f2;
    --line:rgba(255,255,255,0.07);
  }
  *{box-sizing:border-box;margin:0;padding:0}
  html,body{width:1200px;height:857px;overflow:hidden;background:var(--backdrop)}
  body{font-family:"Bebas Neue",Impact,sans-serif;position:relative}
  .cover{position:absolute;top:78px;width:540px;height:700px;background:var(--charcoal);overflow:hidden}
  .cover--back{left:40px}
  .cover--front{left:620px}
  .cover__lines{position:absolute;inset:0}
  .title{position:absolute;left:44px;color:var(--white);font-size:34px;line-height:1;letter-spacing:.5px}
  .title__rule{display:block;width:36px;height:2px;background:var(--gold);margin:16px 0 14px}
  .title__products{color:var(--gold);font-size:46px;line-height:1}
  .brand{position:absolute;display:flex;align-items:center;gap:14px;color:var(--white);font-size:26px;line-height:1.1}
  .brand__mark{width:58px;height:58px;border-radius:50%;border:5px solid var(--gold);flex:none}
  .tile{position:absolute;width:120px;height:125px}
  .tile--gold{background:var(--gold)}
  .photo{position:absolute}
  .band{position:absolute;left:0;right:0;bottom:0;height:95px;background:var(--gold)}
  .web{position:absolute;font-size:20px;letter-spacing:.3px}
  .web--front{right:30px;bottom:26px;color:var(--charcoal)}
  .web--back{left:44px;bottom:38px;color:var(--gold)}
  .phones{position:absolute;left:44px;bottom:80px;color:var(--white);font-size:32px;line-height:.95}
  .spine-strip{position:absolute;right:12px;width:56px}
</style>
</head>
<body>

<!-- Back cover -->
<section class="cover cover--back">
  <svg class="cover__lines" width="540" height="700" aria-hidden="true">
    <line x1="120" y1="0" x2="540" y2="620" stroke="var(--line)"/>
    <line x1="320" y1="0" x2="540" y2="330" stroke="var(--line)"/>
    <line x1="0" y1="300" x2="300" y2="700" stroke="var(--line)"/>
  </svg>
  <div class="title" style="top:100px">
    Rubber &amp;<br>Plastic Extursion
    <span class="title__rule"></span>
    <div class="title__products">Gaskets,<br>Trims &amp; Seals</div>
  </div>
  <div class="photo" role="img" aria-label="Coiled rubber and plastic extrusion profiles in red, brown and white" style="left:330px;top:270px;width:130px;height:140px;background:linear-gradient(135deg,#f2f0ee,#b0543a 55%,#6b3526)"></div>
  <div class="spine-strip tile--gold" style="top:120px;height:130px"></div>
  <div class="spine-strip photo" role="img" aria-label="Dark extruded rubber seal profile" style="top:270px;height:140px;background:linear-gradient(160deg,#dad8d6,#3a3030 60%,#b43030)"></div>
  <div class="spine-strip photo" role="img" aria-label="Industrial machinery against blue sky" style="top:420px;height:150px;background:linear-gradient(180deg,#4f86b8,#c88a3a)"></div>
  <div class="spine-strip tile--gold" style="top:580px;height:120px"></div>
  <div class="brand" style="left:44px;top:462px">
    <span class="brand__mark"></span>
    <span>Paragon<br>Polymers</span>
  </div>
  <div class="phones">888-555-0142<br>330-555-0187</div>
  <div class="web web--back">www.paragonpolymers.com</div>
</section>

<!-- Front cover -->
<section class="cover cover--front">
  <svg class="cover__lines" width="540" height="700" aria-hidden="true">
    <line x1="240" y1="0" x2="540" y2="450" stroke="var(--line)"/>
    <line x1="0" y1="260" x2="300" y2="700" stroke="var(--line)"/>
    <line x1="380" y1="0" x2="540" y2="240" stroke="var(--line)"/>
  </svg>
  <div class="brand" style="left:44px;top:44px">
    <span class="brand__mark"></span>
    <span>Paragon<br>Polymers</span>
  </div>
  <div class="title" style="top:168px">
    Rubber &amp;<br>Plastic Extursion
    <span class="title__rule"></span>
    <div class="title__products">Gaskets,<br>Trims &amp; Seals</div>
  </div>

  <div class="band"></div>

  <div class="tile photo" role="img" aria-label="Motorhome on a desert road" style="left:405px;top:105px;background:linear-gradient(180deg,#6fa0d6,#b57a52 55%,#6f6f70)"></div>
  <div class="tile photo" role="img" aria-label="Black rubber gasket profiles" style="left:275px;top:240px;background:linear-gradient(135deg,#f2f2f2,#3b3940 55%,#e8e8e8)"></div>
  <div class="tile photo" role="img" aria-label="Robotic assembly line in a factory" style="left:405px;top:240px;background:linear-gradient(150deg,#c9d6e2,#e0b53a 50%,#8aa0b4)"></div>
  <div class="tile tile--gold" style="left:145px;top:375px"></div>
  <div class="tile photo" role="img" aria-label="Refinery reflected in water" style="left:275px;top:375px;background:linear-gradient(180deg,#7fa9cf,#a98a6a 55%,#5d7f9f)"></div>
  <div class="tile tile--gold" style="left:405px;top:375px"></div>
  <div class="tile photo" role="img" aria-label="Speedboat on open sea" style="left:15px;top:510px;background:linear-gradient(180deg,#a8c6e2,#2f6fa0 45%,#1f4d78)"></div>
  <div class="tile photo" role="img" aria-label="Combine harvester in a field" style="left:145px;top:510px;background:linear-gradient(180deg,#93b8dc,#e0b83a 60%,#9b7b3a)"></div>
  <div class="tile photo" role="img" aria-label="Modern glass office building" style="left:275px;top:510px;background:linear-gradient(160deg,#5d8fc4,#dfe6ee 55%,#5f8a4a)"></div>
  <div class="tile photo" role="img" aria-label="Silver car at sunset" style="left:405px;top:510px;background:linear-gradient(160deg,#6f9fd0,#c8ccd2 55%,#e0b24a)"></div>

  <div class="web web--front">www.paragonpolymers.com</div>
</section>

</body>
</html>
```